Tall Finch Vodka

We are launching a new mainstream Vodka brand "Tall Finch" to take on big brands. China will be first market. The category norms seems to be Red and Black on a clear bottle and we would expect some red but does not need to be entirely red. The design would need to work on both clear (Valdorin) and frosted (Blue Heron) style bottles. In the future we will have gold finch, silver finch, platinum finch and diamond finch for more premium variants.

Target Market(s)

China

Industry/Entity Type

Alcohol

Colors
EB3D1F
EC4F4E
F09395
F8D3D4
FCEDEE

Requirements
Must have
• Space for Chinese language as well ad English
Nice to have
• Energetic, Engaging
Should not have
• Not stereotypes of photo of bad looking bear. Good looking bear, light not heavy.

```html
<!DOCTYPE html>
<html lang="en">
<head>
<meta charset="utf-8">
<title>Tall Finch Vodka – Label</title>
<link rel="stylesheet" href="https://fonts.googleapis.com/css2?family=Lexend:wght@600&family=Barlow:wght@600&display=swap">
<style>
  :root {
    --label-red: #ff0000;
    --panel-black: #000000;
    --trim-gold: #e0b41c;
  }
  html, body {
    margin: 0;
    padding: 0;
    width: 1200px;
    height: 1200px;
    overflow: hidden;
    background: var(--label-red);
  }
  .label {
    display: block;
    width: 1200px;
    height: 1200px;
  }
  .label__ground { fill: var(--label-red); }
  .label__arch {
    fill: var(--panel-black);
    stroke: var(--trim-gold);
    stroke-width: 2.5;
  }
  .label__brand {
    font-family: "Lexend", "Arial Black", sans-serif;
    font-weight: 600;
    font-size: 150px;
    fill: var(--trim-gold);
  }
  .label__frame {
    fill: none;
    stroke: var(--trim-gold);
    stroke-width: 2;
  }
  .label__category {
    font-family: "Barlow", "Arial", sans-serif;
    font-weight: 600;
    font-size: 74px;
    letter-spacing: 0.32em;
    fill: var(--trim-gold);
  }
  .label__spec {
    font-family: "Barlow", "Arial", sans-serif;
    font-weight: 600;
    font-size: 22px;
    letter-spacing: 0.08em;
    fill: var(--trim-gold);
  }
</style>
</head>
<body>
<svg class="label" viewBox="0 0 1200 1200" xmlns="http://www.w3.org/2000/svg">
  <defs>
    <linearGradient id="mascot-tone" x1="0" y1="0" x2="0" y2="1">
      <stop offset="0%" stop-color="#e00000"/>
      <stop offset="60%" stop-color="#a00000"/>
      <stop offset="100%" stop-color="#000000"/>
    </linearGradient>
    <path id="brand-arc" d="M 243.5 684 A 362 362 0 1 1 956.5 684"/>
  </defs>

  <rect class="label__ground" x="0" y="0" width="1200" height="1200"/>

  <path class="label__arch" d="M 56 1144 L 56 600 A 544 544 0 0 1 1144 600 L 1144 1144 Z"/>

  <rect class="label__mascot" role="img" aria-label="Red engraved-style illustration of the brand mascot, head and shoulders"
        x="330" y="320" width="540" height="560" rx="24" fill="url(#mascot-tone)"/>

  <text class="label__brand">
    <textPath href="#brand-arc" startOffset="0" textLength="1180" lengthAdjust="spacing">TALL FINCH</textPath>
  </text>

  <path class="label__frame" d="M 191 663 L 191 1009 L 400 1009"/>
  <path class="label__frame" d="M 1009 663 L 1009 1009 L 800 1009"/>

  <text class="label__category" x="612" y="1034" text-anchor="middle">VODKA</text>

  <text class="label__spec" x="191" y="1036">500 ML</text>
  <text class="label__spec" x="1010" y="1036" text-anchor="end">40% VOL</text>
</svg>
</body>
</html>
```